Package Design for a Grow Your Own Bonsai tree kit

I would like a package redesign of a bonsai tree kit I currently sell. I want it to look modern unique and beautiful. It’s a gift item, so the way the box is presented is important.

I plan to launch several similar plant kits so would like a design that’s transferable to other products. I’d like to incorporate the colour green-and browns - naturalcolours

Target Market(s)

The target market are millennials living in small spaces - without an out door garden or easy access to nature

Industry/Entity Type

Gardener

Font styles to use
Sans Serif

Colors
faa54b
00a990
9bcb3b

Requirements
Must have
• Fresh, clean modern look
Nice to have
• I have included 3 images of bonsai kits below. I like the 1st 2 pictures- they are original and professional and very appealing. The green and white product is my existing packaging. I want to look more professionally desgned

```html
<!DOCTYPE html>
<html lang="en">
<head>
<meta charset="utf-8">
<title>Bonsai Tree Kit – Seed Starter Pack</title>
<link href="https://fonts.googleapis.com/css2?family=Amatic+SC:wght@700&family=Oswald:wght@500&family=Cabin:wght@500;700&display=swap" rel="stylesheet">
<style>
  :root {
    --backdrop: #dcdcdc;
    --panel: #ffffff;
    --leaf: #5aa526;
    --leaf-light: #9bcb3b;
    --orange: #f26b1d;
    --ink: #3a3a3a;
    --rule: #555555;
    --card: #f1f1f1;
  }
  * { box-sizing: border-box; margin: 0; padding: 0; }
  html, body { width: 1200px; height: 789px; overflow: hidden; }
  body {
    background: var(--backdrop);
    font-family: "Cabin", sans-serif;
    display: flex;
    align-items: center;
    justify-content: center;
  }
  .dieline { display: flex; gap: 0; box-shadow: 0 12px 30px rgba(0,0,0,.12); }
  .panel {
    position: relative;
    background: var(--panel);
    height: 460px;
    border-top: 12px solid var(--leaf);
    border-bottom: 12px solid var(--leaf);
  }
  .panel::before, .panel::after {
    content: "";
    position: absolute;
    left: 8px; right: 8px;
    border-top: 2px dotted var(--orange);
  }
  .panel::before { top: 12px; }
  .panel::after { bottom: 12px; }

  /* Side panel */
  .side { width: 230px; padding: 30px 14px 30px; border-right: 1px solid #e4e4e4; }
  .side-head { display: flex; align-items: center; gap: 10px; margin-bottom: 14px; }
  .brand-small { font-family: "Cabin", sans-serif; font-weight: 700; color: var(--leaf); font-size: 17px; line-height: 1; width: 70px; }
  .side-title { font-family: "Oswald", sans-serif; color: var(--orange); line-height: 1.05; }
  .side-title .big { font-size: 22px; display: block; }
  .side-title .small { font-size: 11px; display: block; }
  .species-grid {
    background: var(--card);
    height: 340px;
    position: relative;
  }
  .species { position: absolute; width: 60px; text-align: center; }
  .species .art { width: 46px; height: 110px; margin: 0 auto; border-radius: 6px 6px 10px 10px; }
  .species .tag {
    display: block; margin-top: 4px;
    background: var(--leaf); color: #fff;
    font-family: "Oswald", sans-serif; font-size: 7px; letter-spacing: .5px; padding: 2px 0;
  }

  /* Front panel */
  .front { width: 760px; padding: 0 40px; display: flex; align-items: center; }
  .front-copy { width: 340px; display: flex; flex-direction: column; align-items: center; }
  .brand {
    font-family: "Cabin", sans-serif; font-weight: 700;
    color: var(--leaf); font-size: 52px; line-height: 1;
    display: flex; align-items: center; gap: 12px;
  }
  .brand-dot { width: 14px; height: 14px; border-radius: 50%; background: var(--leaf); }
  .brand-sub { font-family: "Cabin", sans-serif; font-weight: 700; color: var(--leaf); font-size: 20px; margin-top: 6px; }
  .includes {
    font-family: "Amatic SC", sans-serif; font-weight: 700;
    font-size: 44px; line-height: 1; margin-top: 40px; text-align: center;
  }
  .includes .line1 { color: var(--leaf); display: block; padding-bottom: 6px; border-bottom: 2px solid var(--rule); }
  .includes .line2 { color: var(--orange); display: block; padding-top: 6px; }
  .ribbon {
    margin-top: 26px; width: 300px; height: 38px;
    background: var(--leaf); color: #fff;
    font-size: 22px; font-weight: 500;
    display: flex; align-items: center; justify-content: center;
    clip-path: polygon(0 0, 100% 0, 96% 50%, 100% 100%, 0 100%, 4% 50%);
  }
  .hero-art {
    margin-left: 30px; width: 330px; height: 380px;
    background: radial-gradient(ellipse at 50% 40%, #7c9a5a 0%, #a9b59c 45%, #f2f2f2 75%);
    border-radius: 8px;
  }
</style>
</head>
<body>
  <main class="dieline">
    <section class="panel side">
      <header class="side-head">
        <span class="brand-small">Leafy Loft</span>
        <h2 class="side-title"><span class="big">5 BEAUTIFUL</span><span class="small">NATURAL BONSAI TREES</span></h2>
      </header>
      <div class="species-grid">
        <figure class="species" style="left:10px;top:10px"><div class="art" role="img" aria-label="Red maple bonsai in a terracotta pot" style="background:linear-gradient(#d9262a 55%,#b2773f 55%)"></div><span class="tag">SEED NAME</span></figure>
        <figure class="species" style="left:130px;top:10px"><div class="art" role="img" aria-label="Green conifer bonsai in a terracotta pot" style="background:linear-gradient(#3f8a2f 60%,#b2773f 60%)"></div><span class="tag">SEED NAME</span></figure>
        <figure class="species" style="left:70px;top:110px"><div class="art" role="img" aria-label="White blossom bonsai in a terracotta pot" style="background:linear-gradient(#d8e4cf 55%,#b2773f 55%)"></div><span class="tag">SEED NAME</span></figure>
        <figure class="species" style="left:10px;top:200px"><div class="art" role="img" aria-label="Pine bonsai in a terracotta pot" style="background:linear-gradient(#5d7a4a 55%,#b2773f 55%)"></div><span class="tag">SEED NAME</span></figure>
        <figure class="species" style="left:130px;top:210px"><div class="art" role="img" aria-label="Pink blossom bonsai in a terracotta pot" style="background:linear-gradient(#e0336d 55%,#b2773f 55%)"></div><span class="tag">SEED NAME</span></figure>
      </div>
    </section>

    <section class="panel front">
      <div class="front-copy">
        <h1 class="brand"><span class="brand-dot"></span>Leafy Loft</h1>
        <p class="brand-sub">Bonsai Tree Kit</p>
        <p class="includes"><span class="line1">INCLUDES 5 TREE</span><span class="line2">SPECIES TO PLANT</span></p>
        <p class="ribbon">Seed Starter Pack</p>
      </div>
      <div class="hero-art" role="img" aria-label="Illustration of a flowering bonsai tree with a twisting trunk in a white pot"></div>
    </section>
  </main>
</body>
</html>
```